Business card design Needed for new logo / Construction business, home extensions and new builds

We need a business card design using our new logo files which i will attach to this project :)

We are a small construction business specialising in home extensions, new builds and property development. We are very ambitious and would appreciate professional and elegant designs for our new business card.

Very serious about using the services on MakerQuarry and recently acquired our new logo from here :)

Please get involved, i will feedback when i can as i am very busy but can respond daily, thanks

Target Market(s)

People that want to build onto their houses, new building developments or adding too their existing property

Industry/Entity Type

Construction

Contact Information for Business Card

Renwick Tolliver Construction, Lionel Ashby (Managing Director), Tel 07822254961, email - info@renwick-tolliver, www.renwick-tolliver.co.uk

Colors

Designer to choose colors to be used in the design.

Requirements
Must have
• I like a deep grey on the back please. A lot of you have provided black from and back, try mixing things up a little. The black looks cool 😎 Thanks

```html
<!DOCTYPE html>
<html lang="en">
<head>
<meta charset="utf-8">
<title>Renwick Tolliver Construction – Business Card</title>
<link rel="stylesheet" href="https://fonts.googleapis.com/css2?family=Cinzel:wght@600&family=Montserrat:wght@400&display=swap">
<style>
  :root {
    --backdrop: #2b2b2b;
    --card-grey: #666666;
    --card-white: #ffffff;
    --gold: #c9962e;
    --gold-light: #e7c06a;
    --silver: #d6d6d6;
    --ink: #333333;
    --muted: #4a4a4a;
  }
  * { box-sizing: border-box; margin: 0; padding: 0; }
  html, body { width: 1200px; height: 900px; overflow: hidden; }
  body {
    background: var(--backdrop);
    display: flex;
    flex-direction: column;
    align-items: center;
    justify-content: center;
    gap: 34px;
  }
  .card {
    position: relative;
    width: 720px;
    height: 410px;
    border-left: 3px solid var(--gold);
    border-bottom: 3px solid var(--gold);
    box-shadow: 0 10px 24px rgba(0,0,0,0.45);
  }
  .card--back { background: var(--card-grey); }
  .card--front { background: var(--card-white); }

  .wordmark {
    font-family: "Cinzel", serif;
    font-weight: 600;
    letter-spacing: 0.06em;
    text-transform: uppercase;
    line-height: 1.15;
  }
  .card--back .wordmark {
    position: absolute;
    top: 90px;
    right: 50px;
    width: 330px;
    text-align: center;
    font-size: 30px;
    color: var(--silver);
  }
  .card--front .wordmark {
    position: absolute;
    top: 48px;
    left: 44px;
    width: 230px;
    font-size: 20px;
    color: var(--gold);
  }

  .contact-list {
    position: absolute;
    left: 44px;
    bottom: 56px;
    list-style: none;
    font-family: "Montserrat", sans-serif;
    font-size: 20px;
    color: var(--ink);
  }
  .contact-list li {
    display: flex;
    align-items: center;
    gap: 12px;
    margin-top: 12px;
  }
  .contact-icon { width: 16px; height: 16px; flex: none; }

  .person {
    position: absolute;
    right: 48px;
    top: 200px;
    text-align: right;
  }
  .person-name {
    font-family: "Cinzel", serif;
    font-weight: 600;
    font-size: 30px;
    letter-spacing: 0.04em;
    color: var(--gold);
  }
  .person-role {
    font-family: "Montserrat", sans-serif;
    font-size: 20px;
    color: var(--muted);
    letter-spacing: 0.04em;
    margin-top: 2px;
  }
</style>
</head>
<body>
  <section class="card card--back" aria-label="Card back">
    <p class="wordmark">Renwick Tolliver Construction</p>
  </section>

  <section class="card card--front" aria-label="Card front">
    <p class="wordmark">Renwick Tolliver Construction</p>

    <div class="person">
      <p class="person-name">Lionel Ashby</p>
      <p class="person-role">Managing Director</p>
    </div>

    <ul class="contact-list">
      <li>
        <svg class="contact-icon" viewBox="0 0 16 16" aria-hidden="true">
          <path d="M4 1.5l2.2 3-1.3 1.5c.8 1.8 2.3 3.3 4.1 4.1l1.5-1.3 3 2.2-1 2.5C7 13.5 2.5 9 1.5 2.5z" fill="var(--gold)"/>
        </svg>
        07822254961
      </li>
      <li>
        <svg class="contact-icon" viewBox="0 0 16 16" aria-hidden="true">
          <rect x="1" y="3" width="14" height="10" rx="1" fill="var(--gold)"/>
          <path d="M1.5 3.5L8 9l6.5-5.5" fill="none" stroke="#fff" stroke-width="1.3"/>
        </svg>
        info@renwick-tolliver
      </li>
      <li>
        <svg class="contact-icon" viewBox="0 0 16 16" aria-hidden="true">
          <circle cx="8" cy="8" r="7" fill="var(--gold)"/>
          <path d="M1 8h14M8 1c-3 3.5-3 10.5 0 14M8 1c3 3.5 3 10.5 0 14" fill="none" stroke="#fff" stroke-width="1"/>
        </svg>
        www.renwick-tolliver.co.uk
      </li>
    </ul>
  </section>
</body>
</html>
```